Business card for my new company (Accounting firm)

I need a business card for my new business Brightwell Advisory and Ledger SA. Our services are accounting, tax, audit and financial management. Our customers are small companies, start-ups and new companies. The final design has to show financial security, trust and growth. Please find our logo attached to the business card. Text for the business card: Brightwell Advisory and Ledger SA Tomas Varenholt Director and Founder Certified Accountant Tel. 022 418 57 34 tv@clairevalconseil.ch www.clairevalconseil.ch Rue des Vergières 27 1201 Geneva
Target Market(s)
Our customers are small companies, start-ups and new companies.
Industry/Entity Type
Finance And Accounting
Contact Information for Business Card
Claireval Conseil et Comptes SA
Tomas Varenholt
Directeur et Fondateur
Expert-comptable diplômé
Tél. 022 418 57 34
tv@clairevalconseil.ch
www.clairevalconseil.ch
Rue des Vergières 27
1201 Genève

```html
<!DOCTYPE html>
<html lang="fr">
<head>
<meta charset="utf-8">
<title>Claireval Conseil et Comptes – Carte de visite</title>
<link rel="stylesheet" href="https://fonts.googleapis.com/css2?family=Montserrat:wght@500;600&family=Roboto:wght@400;500;700&display=swap">
<style>
  :root {
    --bg: #e4e4e4;
    --blue-light: #2aa3d8;
    --blue: #1f7fb8;
    --blue-deep: #1a5d8f;
    --name-blue: #1c5f9a;
    --ink: #2f3135;
    --grey-text: #4a4c50;
    --strip-dark: #3a3b3e;
    --paper: #f7f7f6;
    --white: #ffffff;
  }
  * { box-sizing: border-box; margin: 0; padding: 0; }
  html, body { width: 1200px; height: 726px; overflow: hidden; }
  body {
    background: var(--bg);
    font-family: "Roboto", Arial, sans-serif;
    position: relative;
  }
  .card {
    position: absolute;
    top: 208px;
    width: 520px;
    height: 310px;
    border-radius: 3px;
    box-shadow: 0 10px 24px rgba(0,0,0,0.18);
    overflow: hidden;
  }
  /* Back face */
  .card--back {
    left: 50px;
    background: linear-gradient(160deg, var(--blue-light) 0%, var(--blue) 45%, var(--blue-deep) 100%);
    color: var(--white);
    display: flex;
    flex-direction: column;
    align-items: center;
    justify-content: center;
  }
  .brand {
    font-family: "Montserrat", Arial, sans-serif;
    font-weight: 600;
    text-transform: uppercase;
    line-height: 1;
  }
  .card--back .brand-name { font-size: 44px; letter-spacing: 6px; }
  .card--back .brand-sub {
    font-family: "Montserrat", Arial, sans-serif;
    font-weight: 600;
    text-transform: uppercase;
    font-size: 13px;
    letter-spacing: 4.5px;
    margin-top: 8px;
  }
  .card--back .site {
    margin-top: 52px;
    font-size: 15px;
    font-weight: 500;
    letter-spacing: 0.3px;
  }
  /* Front face */
  .card--front {
    left: 630px;
    background: var(--paper);
    display: flex;
  }
  .edge-band {
    width: 42px;
    background: linear-gradient(180deg, var(--blue-light) 0%, var(--blue-deep) 100%);
  }
  .edge-rule { width: 6px; background: var(--strip-dark); }
  .front-body { flex: 1; padding: 44px 30px 0 36px; position: relative; }
  .logo-row { display: flex; align-items: center; gap: 14px; }
  .logo-square { width: 40px; height: 40px; background: var(--blue); }
  .front-brand .brand-name { font-size: 38px; letter-spacing: 4px; color: var(--ink); }
  .front-brand .brand-sub {
    font-family: "Montserrat", Arial, sans-serif;
    font-weight: 600;
    text-transform: uppercase;
    font-size: 11px;
    letter-spacing: 3.2px;
    color: var(--ink);
    margin-top: 5px;
  }
  .person { margin-top: 40px; }
  .person-name { font-size: 21px; font-weight: 700; color: var(--name-blue); }
  .person-role { font-size: 12.5px; color: var(--grey-text); line-height: 1.35; margin-top: 4px; }
  .contacts { margin-top: 16px; font-size: 13px; color: var(--ink); }
  .contact-line { display: flex; align-items: center; gap: 14px; margin-bottom: 7px; }
  .contact-item { display: flex; align-items: center; gap: 6px; white-space: nowrap; }
  .icon { width: 13px; height: 13px; fill: var(--name-blue); flex: none; }
</style>
</head>
<body>

  <section class="card card--back" aria-label="Verso de la carte">
    <div class="brand brand-name">Claireval</div>
    <div class="brand-sub">Conseil et Comptes</div>
    <div class="site">www.clairevalconseil.ch</div>
  </section>

  <section class="card card--front" aria-label="Recto de la carte">
    <div class="edge-band"></div>
    <div class="edge-rule"></div>
    <div class="front-body">
      <div class="logo-row">
        <div class="logo-square"></div>
        <div class="front-brand">
          <div class="brand brand-name">Claireval</div>
          <div class="brand-sub">Conseil et Comptes</div>
        </div>
      </div>

      <div class="person">
        <div class="person-name">Tomas Varenholt</div>
        <div class="person-role">Directeur et Fondateur<br>Expert-comptable diplômé</div>
      </div>

      <div class="contacts">
        <div class="contact-line">
          <span class="contact-item">
            <svg class="icon" viewBox="0 0 16 16"><path d="M3.6 1.2l2.3 2.6-1.3 1.9c.9 2 2.6 3.7 4.6 4.6l1.9-1.3 2.6 2.3-1.2 2.3C7.3 14.4 1.6 8.7 1.4 3z"/></svg>
            022 418 57 34
          </span>
          <span class="contact-item">
            <svg class="icon" viewBox="0 0 16 16"><path d="M1 3h14v10H1z M2.2 4.2L8 8.6l5.8-4.4z" fill-rule="evenodd"/></svg>
            tv@clairevalconseil.ch
          </span>
          <span class="contact-item">
            <svg class="icon" viewBox="0 0 16 16"><path d="M8 1a7 7 0 100 14A7 7 0 008 1zm0 1.4c.9 0 1.9 1.7 2.2 4.1H5.8C6.1 4.1 7.1 2.4 8 2.4zM2.5 7.5h2.1c0 .4 0 .7.1 1H2.5zm8.9 0h2.1v1h-2.1zm-5.6 2h4.4c-.3 2.4-1.3 4.1-2.2 4.1s-1.9-1.7-2.2-4.1z"/></svg>
            www.clairevalconseil.ch
          </span>
        </div>
        <div class="contact-line">
          <span class="contact-item">
            <svg class="icon" viewBox="0 0 16 16"><path d="M8 1a5 5 0 00-5 5c0 3.8 5 9 5 9s5-5.2 5-9a5 5 0 00-5-5zm0 7a2 2 0 110-4 2 2 0 010 4z"/></svg>
            Rue des Vergières 27 1201 Genève
          </span>
        </div>
      </div>
    </div>
  </section>

</body>
</html>
```